Local Roofing Company Billboard Design

We need a billboard design for an 8' x 32' billboard. This billboard would need to be easily readable and stand out well.
I have uploaded a design that we like - simple, readable, and gets the point across. We do NOT want the $1000 off offer included.
We are looking for a black background with white copy so it will stand out. We want the following on the billboard:
Brindlewick Roofing logo
brindlewick-roofing.example (optional)
555.214.7730 (mandatory)
Photo is optional, depends on how it all lays out
Production file must comply with layout requirements (uploaded).
Target Market(s)
Homeowners
Font styles to use
Other font styles liked:
- match font from logo
Colors
Designer to choose colors to be used in the design.
Requirements
Must have
- Black background, white copy, logo must be large and legible. Colors used must match our logo colors.

```html
<!DOCTYPE html>
<html lang="en">
<head>
<meta charset="utf-8">
<title>Brindlewick Roofing Billboard</title>
<link rel="stylesheet" href="https://fonts.googleapis.com/css2?family=Arvo:wght@700&family=Open+Sans:wght@600;700&display=swap">
<style>
  :root {
    --ink: #000000;
    --paper: #ffffff;
    --ember: #e55a24;
    --badge-navy: #263d73;
    --backdrop: #e9ebee;
  }
  html, body {
    margin: 0;
    padding: 0;
    width: 1200px;
    height: 688px;
    overflow: hidden;
    background: var(--backdrop);
  }
  .canvas {
    position: relative;
    width: 1200px;
    height: 688px;
  }
  .billboard {
    position: absolute;
    left: 0;
    top: 180px;
    width: 1200px;
    height: 327px;
    overflow: hidden;
    background: var(--ink);
  }
  .billboard-shapes {
    position: absolute;
    inset: 0;
    width: 1200px;
    height: 327px;
  }
  .brand-name {
    position: absolute;
    left: 48px;
    top: 170px;
    margin: 0;
    font-family: "Arvo", Georgia, serif;
    font-weight: 700;
    font-size: 47px;
    line-height: 1;
    color: var(--ink);
    white-space: nowrap;
  }
  .website {
    position: absolute;
    left: 62px;
    top: 258px;
    margin: 0;
    font-family: "Open Sans", Arial, sans-serif;
    font-weight: 700;
    font-size: 26px;
    line-height: 1;
    color: var(--ink);
    white-space: nowrap;
  }
  .phone {
    position: absolute;
    right: 36px;
    top: 32px;
    margin: 0;
    font-family: "Open Sans", Arial, sans-serif;
    font-weight: 700;
    font-size: 90px;
    line-height: 1;
    letter-spacing: -1px;
    color: var(--paper);
    white-space: nowrap;
  }
  .tagline {
    position: absolute;
    right: 32px;
    top: 142px;
    margin: 0;
    font-family: "Open Sans", Arial, sans-serif;
    font-weight: 600;
    font-size: 25px;
    line-height: 37.5px;
    color: var(--paper);
    text-align: right;
  }
</style>
</head>
<body>
<main class="canvas">
  <section class="billboard" aria-label="Brindlewick Roofing billboard">
    <svg class="billboard-shapes" viewBox="0 0 1200 327" aria-hidden="true">
      <rect x="0" y="0" width="1200" height="327" fill="var(--ink)"/>
      <polygon class="gable-field" points="0,146 303,0 308,0 997,327 0,327" fill="var(--paper)"/>
      <polygon class="corner-accent" points="0,0 303,0 0,146" fill="var(--ember)"/>
      <polygon class="slope-band" points="308,0 338,0 1027,327 997,327" fill="var(--ember)"/>
      <polygon class="certification-badge" points="717,144 796,223 717,302 638,223" fill="var(--badge-navy)" stroke="var(--paper)" stroke-width="3"/>
    </svg>
    <h1 class="brand-name">Brindlewick Roofing</h1>
    <p class="website">www.brindlewick-roofing.example</p>
    <p class="phone">555.214.7730</p>
    <p class="tagline">We install all<br>types of residential<br>and commercial roofing<br>across Arizona</p>
  </section>
</main>
</body>
</html>
```